Home Security Company Business Card

Looking for a eye catching business card that is non traditional and stands out but yet still looks professional. It should include all the pertinent information such as name, title, address, telephone, e-mail, website address should definitely stand out and then finally the logo.

Target Market(s)

Residential and Commercial accounts mostly upscale accounts

Industry/Entity Type

Security

Contact Information for Business Card

Name
Title
Address
Office #
Cell #
E-mail
Website

Font styles to use
Serif
Sans Serif

Requirements
Must have
• Logo, two sided color configuration
Nice to have
• You decide
Should not have
• There really aren't any.

```html
<!DOCTYPE html>
<html lang="en">
<head>
<meta charset="utf-8">
<title>Ironvale Security Systems — Business Card</title>
<link href="https://fonts.googleapis.com/css2?family=Noto+Serif:wght@400&display=swap" rel="stylesheet">
<style>
  :root {
    --maroon: #7b1416;
    --gold: #ecbf4f;
    --gold-text: #e2b348;
    --paper: #ffffff;
    --backdrop: #efe7d9;
  }
  * { margin: 0; padding: 0; box-sizing: border-box; }
  html, body {
    width: 1189px; height: 1200px; overflow: hidden;
    background: var(--backdrop);
    font-family: "Noto Serif", Georgia, serif;
  }
  .card {
    position: absolute;
    left: 171px; width: 856px; height: 488px;
    background: var(--paper);
    border-radius: 22px;
    overflow: hidden;
    box-shadow: 0 4px 10px rgba(0,0,0,.18);
  }
  .card--front { top: 67px; }
  .card--back { top: 627px; }

  .brand { color: var(--maroon); font-weight: 400; line-height: 1; position: absolute; }
  .brand__name { display: block; letter-spacing: -1px; }
  .brand__sub { display: block; letter-spacing: -0.5px; }
  .brand-mark { position: absolute; background: var(--gold); }

  .card--front .brand-mark { left: 110px; top: 192px; width: 104px; height: 104px; }
  .card--front .brand { left: 262px; top: 186px; }
  .card--front .brand__name { font-size: 82px; }
  .card--front .brand__sub { font-size: 33px; margin-top: 2px; }

  .card--back .brand-mark { left: 181px; top: 112px; width: 120px; height: 120px; }
  .card--back .brand { left: 0; width: 432px; top: 268px; text-align: center; }
  .card--back .brand__name { font-size: 52px; }
  .card--back .brand__sub { font-size: 21px; }

  .divider { position: absolute; left: 432px; top: 65px; width: 1.5px; height: 288px; background: var(--maroon); opacity: .8; }

  .contact { position: absolute; left: 473px; top: 66px; color: var(--maroon); }
  .contact__name { font-size: 35px; line-height: 1.05; }
  .contact__title { font-size: 22px; color: var(--gold-text); line-height: 1; letter-spacing: .5px; }
  .contact__address { margin-top: 30px; font-size: 21.5px; line-height: 1.35; }
  .contact__lines { list-style: none; margin-top: 8px; }
  .contact__line { display: flex; align-items: center; font-size: 21px; height: 31px; letter-spacing: .3px; }
  .contact__icon { width: 22px; height: 22px; margin-right: 17px; flex: none; }
  .contact__web { margin-top: 12px; font-size: 20.5px; color: var(--gold-text); letter-spacing: 1px; }

  .wave { position: absolute; left: 0; bottom: 0; width: 856px; height: 488px; }
</style>
</head>
<body>

<section class="card card--front" aria-label="Card front">
  <span class="brand-mark"></span>
  <div class="brand">
    <span class="brand__name">IRONVALE</span>
    <span class="brand__sub">SECURITY SYSTEMS INC.</span>
  </div>
</section>

<section class="card card--back" aria-label="Card back">
  <svg class="wave" viewBox="0 0 856 488" aria-hidden="true">
    <path d="M0,380 C240,470 520,418 856,376 L856,488 L0,488 Z" fill="var(--maroon)"/>
    <path d="M4,376 C250,455 540,380 846,364 C560,372 280,472 4,376 Z" fill="var(--gold)"/>
  </svg>

  <span class="brand-mark"></span>
  <div class="brand">
    <span class="brand__name">IRONVALE</span>
    <span class="brand__sub">SECURITY SYSTEMS INC.</span>
  </div>

  <div class="divider"></div>

  <div class="contact">
    <div class="contact__name">Marten Cole</div>
    <div class="contact__title">Owner</div>
    <div class="contact__address">PO Box 418 Harbor Road<br>4th Lane, WA 0000 USA</div>
    <ul class="contact__lines">
      <li class="contact__line">
        <svg class="contact__icon" viewBox="0 0 22 22" aria-label="Office phone"><rect width="22" height="22" rx="3" fill="var(--gold)"/><path d="M5 9c0-3 12-3 12 0l-2 1-1-2H8L7 10zM7 11h8l1 6H6z" fill="#fff"/></svg>
        555-014-2290
      </li>
      <li class="contact__line">
        <svg class="contact__icon" viewBox="0 0 22 22" aria-label="Mobile phone"><rect width="22" height="22" rx="3" fill="var(--gold)"/><rect x="7" y="3" width="8" height="16" rx="1.5" fill="#fff"/><rect x="8.5" y="5" width="5" height="5" fill="var(--gold)"/></svg>
        +1 555-014-2291
      </li>
      <li class="contact__line">
        <svg class="contact__icon" viewBox="0 0 22 22" aria-label="Email"><rect width="22" height="22" rx="3" fill="var(--gold)"/><rect x="4" y="6" width="14" height="10" fill="#fff"/><path d="M4 6l7 6 7-6M4 16l5-5M18 16l-5-5" stroke="var(--gold)" stroke-width="1.2" fill="none"/></svg>
        info@ironvaleus.com
      </li>
    </ul>
    <div class="contact__web">www.ironvaleus.com</div>
  </div>
</section>

</body>
</html>
```